New Zealand Marlborough Sauvignon Blanc wine packaging design

We need packaging design for our new wine brand, Dunmore Vale. The wine is a New Zealand Marlborough Sauvignon Blanc. We would like the packaging will portray elegance and style with an understated label. We are looking for a label that portrays the elegance of the French Riviera. The label should be round or pill shaped.
Updates

Industry/Entity Type

Wine

Font styles to use
Serif
Sans Serif

Requirements
Must have
• The words in order of importance: Dunmore Vale, Sauvignon Blanc, Marlborough, New Zealand. It should be fit to the bottle posted in the links
Nice to have
• a pill shape or circular shape
Should not have
• Illustrations of wine bottles, wine glasses, or grapes

```html
<!DOCTYPE html>
<html lang="en">
<head>
<meta charset="utf-8">
<title>Dunmore Vale – Sauvignon Blanc Label</title>
<link rel="stylesheet" href="https://fonts.googleapis.com/css2?family=Cinzel:wght@500;600&family=Montserrat:wght@500;600&display=swap">
<style>
  :root {
    --wine-red: #9c0a0a;
    --gold: #c99a4a;
    --label-white: #fbfbfa;
    --ink: #1a1a1a;
    --sketch-soft: #e9e9e5;
    --sketch-mid: #dcdcd7;
    --pattern-soft: #e2e2de;
    --page: #ecebe8;
  }
  * { margin: 0; padding: 0; box-sizing: border-box; }
  html, body { width: 1196px; height: 1200px; overflow: hidden; }
  body { background: var(--page); position: relative; font-family: "Montserrat", sans-serif; }

  /* Main pill label */
  .main-label {
    position: absolute; left: 150px; top: 180px;
    width: 500px; height: 840px;
    background: var(--label-white);
    border-radius: 250px;
    border: 3px solid var(--gold);
    box-shadow: 0 0 0 5px var(--label-white), 0 10px 30px rgba(0,0,0,.12);
  }
  .main-label__frame {
    position: absolute; inset: 16px;
    border: 5px solid var(--wine-red);
    border-radius: 234px;
  }
  .main-label__mark {
    position: absolute; left: 50%; top: 74px; transform: translateX(-50%);
    width: 42px; height: 42px; border-radius: 50%; background: var(--wine-red);
  }
  .main-label__scene {
    position: absolute; left: 70px; top: 150px; width: 360px; height: 270px;
    background:
      radial-gradient(ellipse 70% 60% at 45% 68%, var(--sketch-mid) 0%, var(--sketch-soft) 45%, rgba(251,251,250,0) 80%),
      var(--label-white);
  }
  .main-label__band {
    position: absolute; left: 30px; right: 30px; top: 432px; height: 78px;
    background: var(--wine-red);
    border-top: 3px solid var(--gold); border-bottom: 3px solid var(--gold);
    display: flex; align-items: center; justify-content: center;
  }
  .brand-name {
    font-family: "Cinzel", serif; font-weight: 500;
    color: var(--label-white); font-size: 38px; letter-spacing: 1px;
  }
  .main-label__pattern {
    position: absolute; left: 60px; right: 60px; top: 530px; height: 34px;
    background: linear-gradient(180deg, var(--label-white), var(--pattern-soft) 50%, var(--label-white));
    border-bottom: 2px solid var(--ink);
  }
  .varietal {
    position: absolute; left: 0; right: 0; top: 588px; text-align: center;
    font-weight: 600; font-size: 19px; letter-spacing: 8px; color: var(--ink);
  }
  .region {
    position: absolute; left: 0; right: 0; top: 630px; text-align: center;
    font-weight: 500; font-size: 18px; color: var(--ink);
  }
  .divider {
    position: absolute; left: 90px; right: 90px; top: 668px; height: 2px; background: var(--ink);
  }
  .divider::after {
    content: ""; position: absolute; left: 50%; top: -4px; width: 9px; height: 9px;
    background: var(--ink); transform: translateX(-50%) rotate(45deg);
  }
  .main-label__fan {
    position: absolute; left: 50%; top: 696px;
    width: 110px; height: 48px;
    border-radius: 0 0 55px 55px / 0 0 48px 48px;
    background: linear-gradient(180deg, #2b2b2b, var(--ink));
    transform: translateX(-50%);
  }

  /* Neck label */
  .neck-label {
    position: absolute; left: 760px; top: 180px;
    width: 300px; height: 300px; border-radius: 50%;
    background: var(--label-white);
    border: 10px solid var(--wine-red);
    box-shadow: 0 0 0 4px var(--label-white), 0 10px 30px rgba(0,0,0,.12);
  }
  .neck-label__mark {
    position: absolute; left: 50%; top: 38px; transform: translateX(-50%);
    width: 34px; height: 34px; border-radius: 50%; background: var(--wine-red);
  }
  .neck-label__name {
    position: absolute; left: 0; right: 0; top: 104px; text-align: center;
    font-family: "Cinzel", serif; font-weight: 600; font-size: 25px; color: var(--ink);
  }
  .neck-label__rule {
    position: absolute; left: 20px; right: 20px; top: 146px; height: 4px; background: var(--wine-red);
  }
  .neck-label__varietal {
    position: absolute; left: 0; right: 0; top: 166px; text-align: center;
    font-weight: 600; font-size: 12px; letter-spacing: 5px; color: var(--ink);
  }
  .neck-label__region {
    position: absolute; left: 0; right: 0; top: 192px; text-align: center;
    font-weight: 500; font-size: 11px; color: var(--ink);
  }
</style>
</head>
<body>
  <section class="main-label">
    <div class="main-label__frame"></div>
    <div class="main-label__mark"></div>
    <div class="main-label__scene" role="img" aria-label="Ink sketch of a Riviera seaside promenade with palm trees and strolling figures"></div>
    <div class="main-label__band"><h1 class="brand-name">DUNMORE VALE</h1></div>
    <div class="main-label__pattern" role="img" aria-label="Black geometric zigzag and diamond ornament band"></div>
    <p class="varietal">SAUVIGNON BLANC</p>
    <p class="region">Marlborough, Nueva Zelanda</p>
    <div class="divider"></div>
    <div class="main-label__fan" role="img" aria-label="Black fan-shaped ornament"></div>
  </section>

  <section class="neck-label">
    <div class="neck-label__mark"></div>
    <p class="neck-label__name">DUNMORE VALE</p>
    <div class="neck-label__rule"></div>
    <p class="neck-label__varietal">SAUVIGNON BLANC</p>
    <p class="neck-label__region">Marlborough, Nueva Zelanda</p>
  </section>
</body>
</html>
```